RTavenor Business Cards & Letterhead

I have a logo but need a design for some new business cards. We are a Design-Build Firm that specializes in the design and construction of commercial projects.
the cards need to be professional. no cartoon stuff.
i would like to have the cards in AI format so I can update the card as needed. Logo is provided.
Our Address is: 4187 Marlowe Ct. Halden Ridge, Vermont 27614

```html
<!DOCTYPE html>
<html lang="en">
<head>
<meta charset="utf-8">
<title>RTavenor Business Card</title>
<link href="https://fonts.googleapis.com/css2?family=Open+Sans:wght@400;600;700&display=swap" rel="stylesheet">
<style>
  :root {
    --backdrop: #303030;
    --card-dark: #212226;
    --brand-blue: #1a7cc6;
    --deep-blue: #0b3f66;
    --mid-blue: #1569a6;
    --logo-grey: #8a8b90;
    --band-grey: #76777c;
    --text-white: #f2f2f2;
  }
  * { box-sizing: border-box; margin: 0; padding: 0; }
  html, body { width: 1200px; height: 780px; overflow: hidden; }
  body {
    background: var(--backdrop);
    font-family: "Open Sans", Arial, sans-serif;
    position: relative;
  }
  .card {
    position: absolute;
    top: 235px;
    width: 540px;
    height: 309px;
    overflow: hidden;
  }
  /* Back side */
  .card-back {
    left: 40px;
    background: radial-gradient(ellipse at 55% 50%, #137bc0 0%, var(--mid-blue) 35%, var(--deep-blue) 100%);
    display: flex;
    align-items: center;
    justify-content: center;
  }
  .card-back .wordmark {
    font-weight: 700;
    font-size: 46px;
    letter-spacing: 1px;
    color: #0c4a78;
  }
  /* Front side */
  .card-front {
    left: 620px;
    background: var(--card-dark);
    color: var(--text-white);
  }
  .card-art { position: absolute; inset: 0; }
  .front-logo {
    position: absolute;
    left: 30px;
    top: 36px;
    display: flex;
    align-items: center;
    gap: 8px;
  }
  .front-logo .logo-square {
    width: 14px;
    height: 14px;
    background: var(--brand-blue);
  }
  .front-logo .wordmark {
    font-weight: 700;
    font-size: 28px;
    line-height: 1;
    color: var(--logo-grey);
    letter-spacing: 0.5px;
  }
  .person {
    position: absolute;
    right: 34px;
    top: 104px;
    text-align: right;
  }
  .person .name {
    font-weight: 700;
    font-size: 24px;
    color: var(--brand-blue);
    letter-spacing: 0.5px;
    line-height: 1.1;
  }
  .person .role {
    font-weight: 600;
    font-size: 14px;
    color: var(--text-white);
    line-height: 1.3;
  }
  .contact {
    position: absolute;
    left: 38px;
    top: 178px;
    font-size: 13px;
    line-height: 1.3;
  }
  .contact .address {
    border-top: 1px solid var(--text-white);
    padding-top: 2px;
    width: 200px;
    margin-bottom: 6px;
  }
  .contact ul { list-style: none; }
  .contact li { display: flex; align-items: center; gap: 7px; height: 16px; }
  .contact svg { width: 10px; height: 10px; flex: none; }
</style>
</head>
<body>

<section class="card card-back" aria-label="Card back">
  <span class="wordmark">RTAVENOR</span>
</section>

<section class="card card-front" aria-label="Card front">
  <svg class="card-art" viewBox="0 0 540 309" aria-hidden="true">
    <defs>
      <radialGradient id="glow" cx="0.5" cy="0.5" r="0.6">
        <stop offset="0" stop-color="#2a9be8"/>
        <stop offset="1" stop-color="#0d4f82"/>
      </radialGradient>
      <linearGradient id="blueLine" x1="0" x2="1">
        <stop offset="0" stop-color="#0f4f86"/>
        <stop offset="0.6" stop-color="#1a86d4"/>
        <stop offset="1" stop-color="#0f4f86"/>
      </linearGradient>
    </defs>
    <rect x="514" y="104" width="26" height="40" fill="url(#glow)"/>
    <line x1="150" y1="160" x2="508" y2="160" stroke="#e6e6e6" stroke-width="1"/>
    <path d="M0 280 H380 L392 266 H540 V272 H396 L384 286 H0 Z" fill="url(#blueLine)"/>
    <path d="M0 292 H384 L396 277 H540 V309 H0 Z" fill="var(--band-grey)"/>
  </svg>

  <div class="front-logo">
    <span class="logo-square"></span>
    <span class="wordmark">RTAVENOR</span>
  </div>

  <div class="person">
    <p class="name">ROWAN TAVENOR</p>
    <p class="role">Founder/President</p>
  </div>

  <div class="contact">
    <p class="address">4187 Marlowe Ct. Halden Ridge,<br>Vermont 27614</p>
    <ul>
      <li><svg viewBox="0 0 10 10"><path d="M2 1 L4 3 L3 4 Q4 6 6 7 L7 6 L9 8 L8 9 Q3 9 1 2 Z" fill="#1a7cc6"/></svg>(555) 555-0148</li>
      <li><svg viewBox="0 0 10 10"><circle cx="5" cy="5" r="4" fill="none" stroke="#1a7cc6" stroke-width="1.2"/><path d="M1 5 H9 M5 1 V9" stroke="#1a7cc6" stroke-width="0.8"/></svg>www.rtavenor.com</li>
      <li><svg viewBox="0 0 10 10"><rect x="1" y="2" width="8" height="6" fill="none" stroke="#1a7cc6" stroke-width="1.2"/><path d="M1 2 L5 6 L9 2" fill="none" stroke="#1a7cc6" stroke-width="1"/></svg>RT@RTavenor.com</li>
    </ul>
  </div>
</section>

</body>
</html>
```